Business card for Eyelash extension salon in Beverly Hills,California USA

We need new business card for our salon in Beverly Hills. The salon name is 'Lashvera' . We would like to have...Business name: Lashvera Name of person: will provide later Address 4720 N.Alder Crest Ave Beverly Hills , CA 90210 Phone: will provide later (Text only) Web: www.lashverastudio.example Snapgrid icon, Circlebook icon follow us for seasonal campaign and news @lashverastudiolounge Design should look elegant, high-end, clean, simple, cohesive with my brand. Please refer my brand board. Business name color will be metallic bronzy color. Im thinking grey background or white background. Thanks

Target Market(s)

25-35. Gender neutral. People who are in Entertainment business industry.
This is High-end Eyelash extension salon in Beverly Hills

Industry/Entity Type

Beauty Salon

Contact Information for Business Card

Business name: Lashvera
Name of person: will provide later
Address 4720 N.Alder Crest Ave Beverly Hills , CA 90210
Phone: will provide later (Text only)
Web: www.lashverastudio.example
Snapgrid icon, Circlebook icon
follow us for seasonal campaign and news @lashverastudiolounge

Requirements
Must have
• Beautiful, elegant, clean and simple look but very attractive and modern
Should not have
• We don't like too clutter, too busy designs.

```html
<!DOCTYPE html>
<html lang="en">
<head>
<meta charset="utf-8">
<title>Lashvera Business Card</title>
<link rel="stylesheet" href="https://fonts.googleapis.com/css2?family=Work+Sans:wght@300;400;600&display=swap">
<style>
  :root {
    --stage: #2e2e30;
    --bronze: #8b6750;
    --ink: #060708;
    --paper-text: #ffffff;
  }
  * { box-sizing: border-box; margin: 0; padding: 0; }
  html, body { width: 1200px; height: 800px; overflow: hidden; }
  body {
    background: var(--stage);
    font-family: "Work Sans", Arial, sans-serif;
    display: flex;
    align-items: center;
    justify-content: center;
    gap: 40px;
  }
  .card {
    position: relative;
    width: 540px;
    height: 309px;
    border-radius: 22px;
    overflow: hidden;
    background: var(--bronze);
    color: var(--paper-text);
  }

  /* Front */
  .card-front { display: flex; }
  .brand-panel {
    position: relative;
    width: 190px;
    height: 100%;
    background: var(--ink);
  }
  .brand-panel .brand-lockup {
    position: absolute;
    left: 50%;
    top: 50%;
    transform: translate(-50%, -50%) rotate(-90deg);
    color: var(--bronze);
    text-align: right;
    white-space: nowrap;
  }
  .brand-name {
    font-weight: 300;
    font-size: 46px;
    letter-spacing: 1px;
    line-height: 1;
  }
  .brand-place {
    font-weight: 300;
    font-size: 8px;
    letter-spacing: 2.5px;
    margin-top: 6px;
  }
  .details {
    padding: 46px 0 0 30px;
    flex: 1;
  }
  .person-name { font-weight: 600; font-size: 25px; letter-spacing: 1.5px; }
  .person-role { font-weight: 300; font-size: 15px; letter-spacing: 1px; margin-top: 2px; }
  .contact { margin-top: 24px; font-size: 14px; font-weight: 400; line-height: 1.4; letter-spacing: 0.6px; }
  .address { margin-top: 22px; font-size: 14px; font-weight: 400; line-height: 1.4; letter-spacing: 0.6px; }
  .address .company { font-weight: 600; }

  /* Back */
  .card-back {
    display: flex;
    align-items: center;
    justify-content: space-between;
    gap: 28px;
    padding: 0 38px 0 32px;
  }
  .social {
    display: flex;
    align-items: center;
    gap: 9px;
    font-size: 10px;
    font-weight: 400;
    letter-spacing: 0.3px;
    white-space: nowrap;
    margin-top: -34px;
  }
  .social-item { display: flex; align-items: center; gap: 4px; }
  .social-dot { width: 8px; height: 8px; border-radius: 50%; background: var(--paper-text); }
  .handle { font-weight: 600; }
  .card-back .brand-lockup {
    text-align: right;
    color: var(--paper-text);
    white-space: nowrap;
    margin-top: 24px;
  }
  .card-back .brand-name { font-size: 44px; }
</style>
</head>
<body>
  <section class="card card-front" aria-label="Card front">
    <div class="brand-panel">
      <div class="brand-lockup">
        <div class="brand-name">Lashvera</div>
        <div class="brand-place">BEVERLY HILLS</div>
      </div>
    </div>
    <div class="details">
      <h1 class="person-name">Noel Harrow</h1>
      <p class="person-role">Director</p>
      <p class="contact">Mobile: 0400 555 017<br>Email: noel@lashverastudio.example</p>
      <p class="address"><span class="company">LASHVERA</span><br>4720 N.Alder Crest Ave<br>Beverly Hills , CA 90210</p>
    </div>
  </section>

  <section class="card card-back" aria-label="Card back">
    <div class="social">
      <span class="social-item"><span class="social-dot"></span>Snapgrid</span>
      <span class="social-item"><span class="social-dot"></span>Circlebook</span>
      <span class="handle">@lashverastudiolounge</span>
    </div>
    <div class="brand-lockup">
      <div class="brand-name">Lashvera</div>
      <div class="brand-place">BEVERLY HILLS</div>
    </div>
  </section>
</body>
</html>
```